Heron Haulage needs Bussiness cards!

Our new trucking company needs business cards!
We need the same design with two different names and emails, everything else it's the same.
I have included our original logo so we can use it for the design.
Note: the logo to be used is the o e with the buffalo on the right side, next to the letters H and H.

Target Market(s)

Trucking, refrigerated transportation, freight

Industry/Entity Type

Business

Contact Information for Business Card

Card #1:
Marcus Whitfield
marcuswhitfield@heronhaulage.example
1-855-317-6094
(956)238-7160
4117 W. Larkin Ave.
Pharr, TX 78590
www.heronhaulage.example

Card#2:
Rosalba Quintero
rosalba@heronhaulage.example
1-855-317-6094
(956)238-7160
4117 W. Larkin Ave.
Pharr, TX 78590
www.heronhaulage.example

Font styles to use
Sans Serif

Colors
0655a3
ec1f27
ffffff

Requirements
Must have
• our logo
Nice to have
• roads on background,

```html
<!DOCTYPE html>
<html lang="en">
<head>
<meta charset="utf-8">
<title>Heron Haulage – Business Card</title>
<link rel="stylesheet" href="https://fonts.googleapis.com/css2?family=Open+Sans:wght@400;700;800&display=swap">
<style>
  :root {
    --navy: #1b3a6e;
    --red: #b6212a;
    --white: #ffffff;
    --ink: #2b2b2b;
    --rule: #c9c9c9;
    --stage: #ecebe8;
  }
  * { margin: 0; padding: 0; box-sizing: border-box; }
  html, body { width: 1200px; height: 1000px; overflow: hidden; }
  body {
    background: var(--stage);
    font-family: "Open Sans", Arial, sans-serif;
    position: relative;
  }
  .card {
    position: absolute;
    left: 265px;
    width: 666px;
    height: 397px;
    background: var(--white);
    overflow: hidden;
    box-shadow: 0 2px 8px rgba(0,0,0,0.18);
  }
  .card--front { top: 73px; }
  .card--back { top: 533px; }

  .brand {
    position: absolute;
    display: flex;
    align-items: center;
    gap: 10px;
    font-weight: 800;
    color: var(--navy);
    white-space: nowrap;
  }
  .brand__dot {
    border-radius: 50%;
    background: var(--red);
    flex: none;
  }
  .card--front .brand { right: 34px; top: 58px; font-size: 42px; }
  .card--front .brand__dot { width: 26px; height: 26px; }

  .person { position: absolute; left: 33px; top: 207px; }
  .person__name {
    font-size: 20px; font-weight: 700; color: var(--navy); letter-spacing: 0.3px;
  }
  .person__title { font-size: 15px; color: var(--ink); margin-top: 1px; }

  .divider {
    position: absolute; left: 33px; top: 267px; width: 460px; height: 1px; background: var(--rule);
  }

  .address {
    position: absolute; left: 33px; top: 293px; font-size: 15px; line-height: 21px; color: var(--ink);
  }

  .contacts {
    position: absolute; right: 30px; top: 256px; list-style: none;
    font-size: 15px; line-height: 24.5px; color: var(--ink); text-align: right;
  }
  .contacts li { display: flex; justify-content: flex-end; align-items: center; gap: 6px; }
  .contacts svg { width: 13px; height: 13px; flex: none; }

  .band { position: absolute; left: 0; bottom: 0; width: 666px; height: 30px; }

  .road-photo {
    position: absolute; inset: 0;
    background:
      linear-gradient(90deg, rgba(255,255,255,0) 55%, rgba(180,190,205,0.55) 100%),
      linear-gradient(180deg, #e6e8ec 0%, #f1f1f0 30%, #c9cbcc 55%, #dcdcdc 100%);
  }
  .card--back .brand {
    left: 130px; top: 170px; font-size: 60px;
  }
  .card--back .brand__dot { width: 36px; height: 36px; }
</style>
</head>
<body>

<section class="card card--front" aria-label="Business card front">
  <div class="brand"><span>Heron Haulage</span><span class="brand__dot"></span></div>

  <div class="person">
    <p class="person__name">MARCUS WHITFIELD</p>
    <p class="person__title">Managing Director</p>
  </div>

  <div class="divider"></div>

  <p class="address">4117 W. Larkin Ave.<br>Pharr, TX 78590</p>

  <ul class="contacts">
    <li>(956)238-7160
      <svg viewBox="0 0 13 13"><rect x="3.5" y="0.5" width="6" height="12" rx="1" fill="none" stroke="var(--navy)" stroke-width="1.3"/><rect x="5" y="2" width="3" height="7" fill="var(--navy)"/></svg>
    </li>
    <li>1-855-317-6094
      <svg viewBox="0 0 13 13"><path d="M1 5 Q6.5 0 12 5 L10 6.5 L9 4.5 L4 4.5 L3 6.5 Z" fill="var(--navy)"/><rect x="2.5" y="7" width="8" height="5" rx="1" fill="var(--navy)"/></svg>
    </li>
    <li>marcuswhitfield@heronhaulage.example
      <svg viewBox="0 0 13 13"><rect x="0.5" y="2.5" width="12" height="8" fill="var(--navy)"/><path d="M0.5 2.5 L6.5 7 L12.5 2.5" fill="none" stroke="var(--white)" stroke-width="1"/></svg>
    </li>
    <li>www.heronhaulage.example
      <svg viewBox="0 0 13 13"><circle cx="6.5" cy="6.5" r="5.8" fill="none" stroke="var(--navy)" stroke-width="1.3"/><ellipse cx="6.5" cy="6.5" rx="2.5" ry="5.8" fill="none" stroke="var(--navy)" stroke-width="1"/><line x1="0.7" y1="6.5" x2="12.3" y2="6.5" stroke="var(--navy)" stroke-width="1"/></svg>
    </li>
  </ul>

  <svg class="band" viewBox="0 0 666 30" preserveAspectRatio="none" aria-hidden="true">
    <polygon points="0,12 330,12 316,28 0,28" fill="var(--navy)"/>
    <polygon points="346,2 666,2 666,30 318,30" fill="var(--red)"/>
    <polygon points="334,12 344,4 327,28 322,28" fill="var(--white)"/>
  </svg>
</section>

<section class="card card--back" aria-label="Business card back">
  <div class="road-photo" role="img" aria-label="Faded photograph of a truck speeding along a highway with motion blur"></div>
  <div class="brand"><span>Heron Haulage</span><span class="brand__dot"></span></div>
</section>

</body>
</html>
```